Business Card for Multi-Brand Sportswear Company

We are looking for a business card which represents our company and the multiple brands within it.

The company: Fen Athletics (LTD)
The brands: Fen, TavaPuni, ElmStretch, Grit and Rain

Employees using these cards would be representing Fen Athletics, rather than any of the individual brands. You will see a current design within the uploaded files, to give some inspiration. The actual text of the brands is not necessary, but the logos should be on there is some format.

Our creative minds on this are stretched, so we are looking for someone to make this their own, and show us what a good business card should look like.

We may like to get these printed with spot gloss, so keep that in mind with your designs.

www.fenathletics.co.uk

Industry/Entity Type

Business

Contact Information for Business Card

Leo Pemberton-Hale
Operations Manager
(+44) 1632 960 418
Leo@fenathletics.co.uk
www.fenathletics.co.uk

Font styles to use
Sans Serif
Other font styles liked:
• Eurostile

Colors
ffffff

Requirements
Nice to have
• Dark (black) background

```html
<!DOCTYPE html>
<html lang="en">
<head>
<meta charset="utf-8">
<title>Fen Athletics – Business Card</title>
<link rel="stylesheet" href="https://fonts.googleapis.com/css2?family=Roboto:wght@400;700&display=swap">
<style>
  :root {
    --backdrop: #3b3b3b;
    --card-white: #ffffff;
    --brand-red: #ed1c24;
    --ink-black: #000000;
    --text-grey: #555555;
    --paper-shadow: rgba(0, 0, 0, 0.45);
  }
  * { margin: 0; padding: 0; box-sizing: border-box; }
  html, body {
    width: 1105px;
    height: 1200px;
    overflow: hidden;
    background: var(--backdrop);
    font-family: "Roboto", Arial, sans-serif;
  }
  .card {
    position: absolute;
    left: 196px;
    width: 720px;
    height: 412px;
    box-shadow: 0 4px 14px var(--paper-shadow);
    overflow: hidden;
  }
  .card--front { top: 145px; background: var(--card-white); }
  .card--back  { top: 602px; background: var(--brand-red); }

  .header-band { position: absolute; top: 0; left: 0; width: 720px; height: 96px; }

  .holder { position: absolute; left: 46px; top: 20px; }
  .holder__name {
    color: var(--brand-red);
    font-weight: 700;
    font-size: 25px;
    letter-spacing: 0.3px;
  }
  .holder__role {
    color: var(--card-white);
    font-size: 20px;
    margin-top: 3px;
  }

  .address {
    position: absolute;
    left: 46px;
    top: 230px;
    color: var(--text-grey);
    font-size: 19px;
    line-height: 26px;
  }
  .contact-list {
    position: absolute;
    left: 46px;
    top: 289px;
    list-style: none;
    color: var(--text-grey);
    font-size: 19px;
    line-height: 27.5px;
  }
  .contact-list li { display: flex; align-items: center; gap: 10px; }
  .contact-list svg { width: 17px; height: 17px; flex: none; }

  .wordmark {
    display: flex;
    align-items: center;
    font-weight: 700;
  }
  .wordmark--front {
    position: absolute;
    right: 40px;
    top: 320px;
    gap: 10px;
    font-size: 34px;
    color: var(--ink-black);
  }
  .wordmark__dot {
    width: 14px;
    height: 14px;
    border-radius: 50%;
    background: var(--brand-red);
  }
  .wordmark--back {
    position: absolute;
    left: 0;
    right: 0;
    top: 140px;
    justify-content: center;
    font-size: 64px;
    color: var(--card-white);
  }
  .brand-row {
    position: absolute;
    left: 0;
    right: 0;
    top: 322px;
    display: flex;
    justify-content: center;
    gap: 28px;
    list-style: none;
    color: var(--card-white);
    font-size: 20px;
    font-weight: 700;
  }
</style>
</head>
<body>
  <section class="card card--front">
    <svg class="header-band" viewBox="0 0 720 96" aria-hidden="true">
      <path d="M0 0 H720 V8 C700 50 690 80 600 86 C520 90 420 92 300 96 H0 Z" fill="var(--brand-red)"/>
      <path d="M0 0 H678 C655 40 640 78 560 86 C470 92 380 94 300 96 H0 Z" fill="var(--ink-black)"/>
    </svg>
    <div class="holder">
      <p class="holder__name">Owen Thackeray</p>
      <p class="holder__role">Managing Director</p>
    </div>
    <address class="address" style="font-style:normal">
      Kestrel Yard, Ashby<br>Ripley, ZZ9 4QT
    </address>
    <ul class="contact-list">
      <li>
        <svg viewBox="0 0 16 16" aria-hidden="true"><path d="M3 1 L6 1 L7 5 L5 6.5 C6 9 7 10 9.5 11 L11 9 L15 10 L15 13 C15 14 14 15 13 15 C6 15 1 10 1 3 C1 2 2 1 3 1 Z" fill="var(--brand-red)"/></svg>
        +44 (0)1632 960418
      </li>
      <li>
        <svg viewBox="0 0 16 16" aria-hidden="true"><rect x="1" y="3" width="14" height="10" fill="var(--brand-red)"/><path d="M1 3 L8 9 L15 3" stroke="#fff" stroke-width="1.4" fill="none"/></svg>
        owen@fenathletics.co.uk
      </li>
      <li>
        <svg viewBox="0 0 16 16" aria-hidden="true"><circle cx="8" cy="8" r="7" fill="var(--brand-red)"/><path d="M4 6 C6 5 7 7 9 6 M6 11 C8 10 10 11 12 9" stroke="#fff" stroke-width="1.3" fill="none"/></svg>
        www.fenathletics.co.uk
      </li>
    </ul>
    <div class="wordmark wordmark--front">
      <span class="wordmark__dot"></span>
      <span>Fen Athletics</span>
    </div>
  </section>

  <section class="card card--back">
    <div class="wordmark wordmark--back">Fen Athletics</div>
    <ul class="brand-row">
      <li>Fen</li>
      <li>TavaPuni</li>
      <li>ElmStretch</li>
      <li>Grit and Rain</li>
    </ul>
  </section>
</body>
</html>
```